Veltaramine™

I need a product label for a 100 ml clear glass vial with a white, blue or red crimp top . The label dimensions are 2" x 6". I am attaching my rough draft, as well as some other art work that might help the designer have a more insight as to what I am seeking. Our printer needs the artwork to be 600x600dpi in resolution. I am open to the idea of our company logo "crestmark biolabs" and the product name "VELTARAMINE™" being in chrome. This product is a site enhancement oil for bodybuilders. I prefer a more "pharma" style look over a gimmicky bodybuilder theme, BUT I am open to anyone's suggestions. After this is concluded, We also want to use the template for the remainder of our supplement line.We will obviously work with the same designer to complete the remaining 6-8 products. I am new to this so if there is anything you need from me to clarify from me, please ask :)

```html
<!DOCTYPE html>
<html lang="en">
<head>
<meta charset="utf-8">
<title>Veltaramine™ Vial Label</title>
<link href="https://fonts.googleapis.com/css2?family=Raleway:wght@400;500;700;800&display=swap" rel="stylesheet">
<style>
  :root {
    --paper: #ffffff;
    --mint: #b3dfcb;
    --mint-deep: #a6d6c2;
    --band: #439e7d;
    --brand-blue: #1a7396;
    --ink: #222222;
    --ink-soft: #333333;
    --white: #ffffff;
    --trim: #e0218a;
    --crop: #111111;
  }
  * { margin: 0; padding: 0; box-sizing: border-box; }
  html, body { width: 1200px; height: 514px; overflow: hidden; background: var(--paper); }
  body { font-family: "Raleway", sans-serif; }
  .canvas { position: relative; width: 1200px; height: 514px; }

  .crop-marks { position: absolute; inset: 0; }

  .label-bleed {
    position: absolute; left: 54px; top: 72px; width: 1084px; height: 390px;
    background: var(--mint); overflow: hidden;
  }
  .molecule-pattern {
    position: absolute; left: 0; top: 0; width: 100%; height: 282px;
    background: radial-gradient(ellipse at 50% 40%, var(--mint) 0%, var(--mint-deep) 100%);
  }
  .info-band {
    position: absolute; left: 0; top: 282px; width: 100%; height: 108px;
    background: var(--band);
  }
  .trim-line {
    position: absolute; left: 77px; top: 94px; width: 1040px; height: 346px;
    border: 1.5px solid var(--trim);
  }

  .centered { position: absolute; transform: translateX(-50%); white-space: nowrap; text-align: center; }

  /* Features column */
  .features-owner { left: 232px; top: 122px; font-size: 21px; font-weight: 500; color: var(--brand-blue); }
  .features-product { left: 232px; top: 150px; font-size: 24px; font-weight: 800; color: var(--brand-blue); letter-spacing: 0.3px; }
  .features-title { left: 232px; top: 181px; font-size: 18px; font-weight: 700; color: var(--brand-blue); }
  .feature-list { list-style: none; }
  .feature-item {
    position: absolute; font-size: 21px; color: var(--ink); white-space: nowrap;
  }
  .feature-item::before {
    content: ""; position: absolute; left: -18px; top: 11px; width: 4px; height: 4px; background: var(--ink);
  }
  .feature-item:nth-child(1) { left: 128px; top: 234px; }
  .feature-item:nth-child(2) { left: 140px; top: 277px; }
  .feature-item:nth-child(3) { left: 170px; top: 321px; }

  /* Centre column */
  .brand-name {
    left: 596px; top: 154px; font-size: 20px; font-weight: 800; color: var(--ink);
    letter-spacing: 2px; display: flex; align-items: center; gap: 10px;
  }
  .brand-dot { width: 12px; height: 12px; border-radius: 50%; background: var(--ink); display: inline-block; }
  .product-name { left: 596px; top: 240px; font-size: 33px; font-weight: 800; color: var(--ink); letter-spacing: 0.5px; }
  .product-rule { position: absolute; left: 502px; top: 291px; width: 188px; height: 2px; background: var(--brand-blue); }
  .product-grade { left: 596px; top: 306px; font-size: 26px; font-weight: 400; color: var(--ink-soft); }
  .contents { left: 596px; top: 382px; font-size: 26px; font-weight: 400; color: var(--white); }

  /* Instructions column */
  .instructions-title { left: 976px; top: 122px; font-size: 26px; font-weight: 500; color: var(--brand-blue); }
  .instructions-text { left: 976px; top: 177px; font-size: 21px; font-weight: 400; color: var(--brand-blue); }
  .shake-illustration {
    position: absolute; left: 946px; top: 228px; width: 74px; height: 122px;
    background: linear-gradient(180deg, #8fc4ae 0%, #7fb8a1 100%); border-radius: 6px;
  }
  .shake-badge { position: absolute; left: 902px; top: 364px; width: 148px; height: 36px; }
  .shake-badge svg { position: absolute; inset: 0; }
  .shake-badge-text {
    position: absolute; left: 0; width: 100%; text-align: center; color: var(--white); line-height: 1;
  }
  .shake-badge-text.strong { top: 3px; font-size: 14px; font-weight: 800; }
  .shake-badge-text.light { top: 22px; font-size: 12.5px; font-weight: 500; letter-spacing: 0.3px; }
</style>
</head>
<body>
<div class="canvas">
  <svg class="crop-marks" width="1200" height="514" viewBox="0 0 1200 514" aria-hidden="true">
    <g stroke="var(--crop)" stroke-width="1">
      <line x1="77" y1="18" x2="77" y2="76"/>
      <line x1="1117" y1="18" x2="1117" y2="76"/>
      <line x1="77" y1="454" x2="77" y2="512"/>
      <line x1="1117" y1="454" x2="1117" y2="512"/>
      <line x1="0" y1="94" x2="54" y2="94"/>
      <line x1="0" y1="440" x2="54" y2="440"/>
      <line x1="1138" y1="94" x2="1200" y2="94"/>
      <line x1="1138" y1="440" x2="1200" y2="440"/>
    </g>
  </svg>

  <div class="label-bleed">
    <div class="molecule-pattern" role="img" aria-label="Faint molecular hexagon pattern background"></div>
    <div class="info-band"></div>
  </div>
  <div class="trim-line"></div>

  <div class="centered features-owner">Crestmark Biolabs’s</div>
  <div class="centered features-product">VELTARAMINE</div>
  <div class="centered features-title">Features:</div>
  <ul class="feature-list">
    <li class="feature-item">Muscle Volumization</li>
    <li class="feature-item">Site Enhancement</li>
    <li class="feature-item">Join Therapy</li>
  </ul>

  <div class="centered brand-name"><span class="brand-dot"></span>CRESTMARK BIOLABS</div>
  <div class="centered product-name">VELTARAMINE™</div>
  <div class="product-rule"></div>
  <div class="centered product-grade">Pharmaceutical Grade</div>
  <div class="centered contents">Contents: 100 ml</div>

  <div class="centered instructions-title">Instructions:</div>
  <div class="centered instructions-text">Shake before use.</div>
  <div class="shake-illustration" role="img" aria-label="Line illustration of a hand shaking a vial"></div>
  <div class="shake-badge">
    <svg width="148" height="36" viewBox="0 0 148 36" aria-hidden="true">
      <polygon points="12,6 0,18 12,30" fill="var(--white)"/>
      <polygon points="136,6 148,18 136,30" fill="var(--white)"/>
    </svg>
    <div class="shake-badge-text strong">SHAKE WELL</div>
    <div class="shake-badge-text light">BEFORE USING</div>
  </div>
</div>
</body>
</html>
```